WP website design (Harrowgate)

We need a wordpress design for an established auction and real estate company based in Florida. The winning design will incorporate a professional color scheme with company logo in a clean layout. The design needs to consider that this will be developed on a responsive theme. Colors are those that will highlight the logo.

Industry/Entity Type

Real Estate

Font styles to use
Serif
Sans Serif

Colors

Designer to choose colors to be used in the design.

Requirements
Must have
• Navigation:
1) Home
2) Auctions
3) Online Auctions
4) About Us
5) Services
6) Real Estate Listings
7) References
8) Contact Us

Colors will be blue (#000066) / red (#B10000) and black or other complementary color. Tagline to be used "Since 1977, Proven Results." Slideshow to be placed in the header or body of home page - please use stock real estate image.

Widgets: 1) Email Sign-up 2) Social media icons for FB and Workline 3) Featured Listings 4) Testimonials 5) Register button

Footer will have smaller company logo, attached logos and contact info:
Phone: (555) 261-0948 Mobile: (555) 718-3062
Email: mirelharrowgate@quellmail.example
Address: 58 E. Tamsin Avenue, Ste 410, Pensacola, FL 32599
Nice to have
• Use of a drop down menu:
Auctions-
1) Upcoming Auctions
2) Past Auctions

```html
<!DOCTYPE html>
<html lang="en">
<head>
<meta charset="utf-8">
<title>Harrowgate Auctions</title>
<link href="https://fonts.googleapis.com/css2?family=Open+Sans:ital,wght@0,400;0,600;0,700;1,400&display=swap" rel="stylesheet">
<style>
:root{
  --navy:#2a2f8f;
  --nav-top:#5a5fc8;
  --nav-bot:#3d42a8;
  --red:#c8161d;
  --red-dark:#a80e14;
  --text:#333;
  --muted:#777;
  --line:#ddd;
  --footer:#2b2b2b;
  --footer-bottom:#1f1f1f;
  --link:#2a2f8f;
}
*{margin:0;padding:0;box-sizing:border-box}
html,body{width:862px;height:1200px;overflow:hidden;background:#fff}
body{font-family:"Open Sans",Arial,sans-serif;color:var(--text);position:relative}
.abs{position:absolute}
/* header */
.brand{left:72px;top:20px;display:flex;align-items:center;gap:10px}
.brand-mark{width:36px;height:36px;background:var(--navy)}
.brand-name{font-size:22px;font-weight:700;color:var(--navy);line-height:1}
.search{left:545px;top:30px;width:127px;height:23px;border:1px solid #ccc;border-radius:2px;font-size:10px;color:#999;padding:4px 7px}
.search svg{position:absolute;right:4px;top:4px}
.btn-sm{top:30px;height:23px;color:#fff;font-size:10px;font-weight:600;display:flex;align-items:center;justify-content:center;border-radius:2px}
.btn-register{left:678px;width:60px;background:var(--navy)}
.btn-login{left:742px;width:48px;background:var(--red)}
/* nav */
.nav{left:0;top:82px;width:862px;height:33px;background:linear-gradient(var(--nav-top),var(--nav-bot))}
.nav ul{list-style:none;display:flex;position:absolute;left:72px;top:0;height:33px}
.nav li{color:#fff;font-size:11px;padding:0 10px;line-height:33px;border-right:1px solid rgba(255,255,255,.25)}
.nav li.active{background:#3a3a3a;padding:0 14px}
/* hero */
.hero{left:0;top:115px;width:862px;height:311px;background:linear-gradient(180deg,#8fb3d9 0%,#c9d7e4 30%,#d9a860 55%,#6b7a3c 80%,#4a5a2c 100%)}
.hero-arrow{top:128px;width:30px;height:60px;background:rgba(255,255,255,.85)}
.hero-arrow.left{left:-15px;border-radius:0 30px 30px 0}
.hero-arrow.right{right:-15px;border-radius:30px 0 0 30px}
.tagline{left:312px;top:272px;width:226px;height:35px;background:rgba(0,0,0,.55);color:#fff;font-size:16px;font-weight:600;text-align:center;line-height:35px}
/* welcome */
.h-red{color:var(--red);font-size:19px;font-weight:400}
.welcome-h{left:72px;top:446px}
.lead{left:72px;top:478px;font-size:12px;color:#333}
.body-copy{left:72px;top:502px;width:532px;font-size:9.5px;line-height:16.5px;color:var(--muted)}
.rule{height:1px;background:var(--line)}
/* sidebar */
.register-now{left:619px;top:451px;width:172px;height:32px;background:linear-gradient(var(--red),var(--red-dark));color:#fff;font-size:14px;font-weight:600;display:flex;align-items:center;justify-content:center;gap:8px}
.newsletter{left:619px;top:489px;width:172px;height:95px;background:var(--nav-bot);color:#fff;padding:10px 12px}
.newsletter h3{font-size:13px;font-weight:600}
.newsletter p{font-size:7px;line-height:11px;margin-top:3px}
.nl-form{display:flex;margin-top:8px;height:21px;border:1px solid #fff}
.nl-form span{flex:1;background:#fff;color:#333;font-size:8.5px;padding:4px 6px}
.nl-form b{background:#3a3a3a;font-size:8.5px;font-weight:400;padding:4px 5px}
.featured-h{left:72px;top:611px}
.pager{top:617px;font-size:12px;color:#777}
.testi-h{left:619px;top:615px;font-size:13px;color:var(--red)}
.testi{left:619px;top:645px;width:171px;height:96px;border:1px solid var(--line);background:#fafafa;padding:8px 14px;font-size:9px;font-style:italic;line-height:15px;color:#777}
.testi-author{left:730px;top:760px;font-size:9.5px;color:var(--link)}
.social{left:619px;width:171px;height:31px;color:#fff;font-size:12px;font-weight:600;display:flex;align-items:center}
.social i{width:30px;height:100%;background:rgba(0,0,0,.15);display:block;margin-right:10px}
.social.one{top:796px;background:linear-gradient(#5a7fc4,#3b5998)}
.social.two{top:838px;background:linear-gradient(#1a8ac0,#0a6a9a)}
/* cards */
.card{width:165px;height:134px;border:1px solid var(--line);padding:4px}
.card .img{height:98px}
.card .name{text-align:center;font-size:9.5px;font-weight:600;color:var(--link);margin-top:9px}
.countdown{position:relative;color:#fff;font-size:9.5px;text-align:center;padding-top:16px}
.countdown .boxes{display:flex;gap:5px;justify-content:center;margin-top:7px}
.countdown .boxes span{background:#fff;color:var(--red);width:38px;height:38px;font-size:13px;line-height:38px}
.countdown small{font-size:6px}
/* partners */
.partner{top:978px;height:50px;background:#e4e4ea;border-radius:3px}
/* footer */
.footer{left:0;top:1052px;width:862px;height:95px;background:var(--footer);color:#ccc;font-size:9.5px}
.footer ul{list-style:none;position:absolute;top:24px;line-height:19.5px}
.footer li::before{content:"•";margin-right:6px;font-size:8px}
.footer .contact{position:absolute;top:24px;line-height:19.5px}
.footer-bottom{left:0;top:1147px;width:862px;height:53px;background:var(--footer-bottom);color:#bbb;font-size:9.5px}
.footer-bottom p{position:absolute;left:72px;top:18px}
.circles{position:absolute;left:672px;top:15px;display:flex;gap:4px}
.circles span{width:20px;height:20px;border-radius:50%;background:#666;display:block}
</style>
</head>
<body>

<div class="abs brand"><span class="brand-mark"></span><span class="brand-name">Harrowgate Auctions</span></div>
<div class="abs search">Search
  <svg width="13" height="13" viewBox="0 0 13 13"><circle cx="5.5" cy="5.5" r="4" fill="none" stroke="#888" stroke-width="1.5"/><line x1="8.5" y1="8.5" x2="12" y2="12" stroke="#888" stroke-width="1.5"/></svg>
</div>
<div class="abs btn-sm btn-register">REGISTER</div>
<div class="abs btn-sm btn-login">LOG IN</div>

<nav class="abs nav"><ul>
  <li class="active">HOME</li><li>AUCTIONS</li><li>ONLINE AUCTIONS</li><li>ABOUT US</li><li>SERVICES</li><li>REAL ESTATE LISTINGS</li><li>REFERENCES</li><li>CONTACT US</li>
</ul></nav>

<div class="abs hero" role="img" aria-label="Slideshow photo of a two-storey stucco house with tiled roof and trees under a blue sky">
  <div class="abs hero-arrow left"><svg class="abs" style="left:18px;top:24px" width="8" height="12"><path d="M7 1L2 6l5 5" stroke="#333" stroke-width="2" fill="none"/></svg></div>
  <div class="abs hero-arrow right"><svg class="abs" style="left:5px;top:24px" width="8" height="12"><path d="M1 1l5 5-5 5" stroke="#333" stroke-width="2" fill="none"/></svg></div>
  <div class="abs tagline">Since 1977, Proven Results</div>
</div>

<h1 class="abs h-red welcome-h">Welcome to Harrowgate</h1>
<p class="abs lead">Morbi auctor odio ut arcu convallis, vitae cursus purus luctus.</p>
<p class="abs body-copy">Mauris nec felis tortor. Fusce sit amet lacus eget velit convallis sodales vitae nec metus. Morbi ante ipsum, condimentum a purus eget, facilisis adipiscing odio. Nullam eu elit diam. Morbi vitae lacinia purus. Donec at ante auctor odio porta blandit et a ligula. Donec imperdiet tortor facilisis elit gravida pulvinar. Donec laoreet arcu quis est rhoncus, rhoncus vulputate sapien venenatis. Proin rutrum vehicula vulputate.</p>
<div class="abs rule" style="left:72px;top:585px;width:532px"></div>

<div class="abs register-now"><svg width="15" height="15"><circle cx="7.5" cy="7.5" r="7.5" fill="#fff"/><path d="M6 4.5l4 3-4 3z" fill="#c8161d"/></svg>REGISTER NOW</div>
<div class="abs newsletter">
  <h3>NEWSLETTER SIGNUP</h3>
  <p>Donec imperdiet tortor facilisis elit gravida pulvinar</p>
  <div class="nl-form"><span>E-mail ID</span><b>Subscribe</b></div>
</div>

<h2 class="abs h-red featured-h">Featured Listings</h2>
<span class="abs pager" style="left:574px">‹</span><span class="abs pager" style="left:593px">›</span>
<h3 class="abs testi-h">TESTIMONIALS</h3>
<span class="abs pager" style="left:781px">›</span>
<blockquote class="abs testi">“ Curabitur viverra ante sit amet aliquam pretium. Phasellus at nibh nibh. Donec sapien eros, consectetur ut tempor nec, laoreet non eros.</blockquote>
<div class="abs testi-author">John Doe, NY</div>
<div class="abs social one"><i></i>Follow on Circlesphere</div>
<div class="abs social two"><i></i>Follow on Workline</div>

<div class="abs card" style="left:72px;top:645px">
  <div class="img countdown" role="img" aria-label="Dark photo of a construction site at dusk" style="background:linear-gradient(#3a4a5a,#1e2a35)">Auction Ends on
    <div class="boxes"><span>3<small>days</small></span><span>12<small>hrs</small></span><span>54<small>sec</small></span></div>
  </div>
  <div class="name">Property name</div>
</div>
<div class="abs card" style="left:255px;top:645px"><div class="img" role="img" aria-label="Photo of a modern white house" style="background:linear-gradient(#4f86d0,#c9ccd2 60%,#7a7f86)"></div><div class="name">Property name</div></div>
<div class="abs card" style="left:438px;top:645px"><div class="img" role="img" aria-label="Photo of a suburban house with green lawn" style="background:linear-gradient(#8fb0d8,#a6a390 45%,#5f9a3a)"></div><div class="name">Property name</div></div>
<div class="abs card" style="left:72px;top:796px"><div class="img" role="img" aria-label="Photo of a large family home at dusk" style="background:linear-gradient(#4a5f9a,#8e8a8c 55%,#4a4a3c)"></div><div class="name">Property name</div></div>
<div class="abs card" style="left:255px;top:796px"><div class="img" role="img" aria-label="Photo of a hand signing a document before glass towers" style="background:linear-gradient(135deg,#1e6fc4,#8cc4ee 60%,#2a4f8f)"></div><div class="name">Property name</div></div>
<div class="abs card" style="left:438px;top:796px"><div class="img" role="img" aria-label="Photo of a city skyline with high-rise towers" style="background:linear-gradient(#5a8ed8,#b9c6d6 55%,#8a8a80)"></div><div class="name">Property name</div></div>

<div class="abs rule" style="left:72px;top:960px;width:719px"></div>
<div class="abs partner" style="left:76px;width:62px"></div>
<div class="abs partner" style="left:147px;width:36px"></div>
<div class="abs partner" style="left:195px;width:150px"></div>
<div class="abs partner" style="left:356px;width:78px"></div>
<div class="abs partner" style="left:441px;width:201px"></div>
<div class="abs partner" style="left:664px;width:120px"></div>

<footer class="abs footer">
  <ul style="left:86px"><li>Home</li><li>Auctions</li><li>Online Auctions</li></ul>
  <ul style="left:191px"><li>About Us</li><li>Services</li><li>Real Estate Listings</li></ul>
  <ul style="left:319px"><li>References</li><li>Contact Us</li></ul>
  <div class="contact" style="left:447px">58 E. Tamsin Avenue, Ste 410,<br>Pensacola, FL 32599<br>Phone : (555) 261-0948</div>
  <div class="contact" style="left:635px">Mobile: (555) 718-3062<br>E-mail : mirelharrowgate@quellmail.example</div>
</footer>
<div class="abs footer-bottom">
  <p>Copyright © 2014 Harrowgate. All rights reserved / Terms and Conditions</p>
  <div class="circles"><span></span><span></span><span></span><span></span><span></span></div>
</div>

</body>
</html>
```